Moderne Visitenkarten für Medizintechnikfirma
Zielgruppe
Vertriebsfirma von moderner und innovativer Medizintechnik
Zielgruppe: Ärzte, Kliniken, Medizintechnikfirmen, Patienten
Aufgabenstellung
Besonderes, modernes, auffälliges und ansprechendes Design ohne überladen oder aufdringlich zu sein
Farbenorientierung kann am Logo und der Website geschehen. Wenn zum Logo harmonierend, sind aber auch andere Farben gerne gesehen.
Format: eher horizontal, vertikal aber auch möglich, abgerundete Ecken einplanen
Wenn möglich folgende Infos bitte schon auf die Karten bringen (pro Person eine Karte):
Konrad Faltermann (CEO)
konrad.faltermann@vitalis-partner.de
(Vitalis Partner GmbH
Lindenhof 12
26210 Grünstedt)
www.vitalis-partner.de
info@vitalis-partner.de
Jonas Prasken (CoS)
jonas.prasken@vitalis-partner.de
Die allgemeinen Firmeninfos können deutlich kleiner sein. Anschrift nur wenn es dadurch nicht zu viel werden würde.

```html
<!DOCTYPE html>
<html lang="de">
<head>
<meta charset="utf-8">
<title>Vitalis Partner – Visitenkarten</title>
<link rel="stylesheet" href="https://fonts.googleapis.com/css2?family=Ubuntu:wght@300;400;500&display=swap">
<style>
  :root {
    --purple: #4b3f7e;
    --orange: #ee5a2a;
    --text-grey: #5a5a6e;
    --label-grey: #555555;
    --card-border: #dcdcdc;
    --page-bg: #ffffff;
  }
  * { margin: 0; padding: 0; box-sizing: border-box; }
  html, body {
    width: 995px;
    height: 1200px;
    overflow: hidden;
    background: var(--page-bg);
    font-family: "Ubuntu", sans-serif;
  }
  .sheet { position: relative; width: 995px; height: 1200px; }
  .format-label {
    position: absolute;
    top: 2px;
    left: 0;
    width: 995px;
    text-align: center;
    font-size: 24px;
    color: var(--label-grey);
  }
  .card {
    position: absolute;
    left: 8px;
    width: 979px;
    height: 518px;
    border: 2px solid var(--card-border);
    background: #fff;
  }
  .card--ceo { top: 62px; }
  .card--cos { top: 642px; }
  .brand-dot {
    position: absolute;
    left: 60px;
    top: 150px;
    width: 140px;
    height: 140px;
    border-radius: 50%;
    background: var(--purple);
  }
  .brand-name {
    position: absolute;
    left: 250px;
    top: 118px;
    font-size: 86px;
    font-weight: 500;
    line-height: 1;
    color: var(--purple);
    letter-spacing: -1px;
  }
  .company-info {
    position: absolute;
    left: 37px;
    top: 344px;
    font-size: 24px;
    line-height: 28px;
    font-weight: 300;
    color: var(--text-grey);
    list-style: none;
  }
  .person {
    position: absolute;
    right: 18px;
    top: 330px;
    text-align: right;
  }
  .person-name {
    font-size: 40px;
    font-weight: 400;
    color: var(--orange);
    line-height: 48px;
  }
  .person-rule {
    display: block;
    margin: 10px 0 14px auto;
    width: 344px;
    height: 4px;
    background: linear-gradient(90deg, rgba(75,63,126,0), var(--purple) 50%, rgba(75,63,126,0));
    border-radius: 2px;
  }
  .person-contact {
    list-style: none;
    font-size: 24px;
    line-height: 30px;
    font-weight: 300;
    color: var(--purple);
  }
</style>
</head>
<body>
<div class="sheet">
  <p class="format-label">size: 90/50 mm</p>

  <section class="card card--ceo">
    <span class="brand-dot"></span>
    <p class="brand-name">Vitalis Partner</p>
    <ul class="company-info">
      <li>Lindenhof 12</li>
      <li>26210 Grünstedt</li>
      <li>www.vitalis-partner.de</li>
      <li>info@vitalis-partner.de</li>
      <li>0800-5513870</li>
    </ul>
    <div class="person">
      <p class="person-name">Konrad Faltermann (CEO)</p>
      <span class="person-rule"></span>
      <ul class="person-contact">
        <li>+4915204417830</li>
        <li>konrad.faltermann@vitalis-partner.de</li>
      </ul>
    </div>
  </section>

  <section class="card card--cos">
    <span class="brand-dot"></span>
    <p class="brand-name">Vitalis Partner</p>
    <ul class="company-info">
      <li>Lindenhof 12</li>
      <li>26210 Grünstedt</li>
      <li>www.vitalis-partner.de</li>
      <li>info@vitalis-partner.de</li>
      <li>0800-5513870</li>
    </ul>
    <div class="person">
      <p class="person-name">Jonas Prasken (CoS)</p>
      <span class="person-rule"></span>
      <ul class="person-contact">
        <li>+4916093327461</li>
        <li>jonas.prasken@vitalis-partner.de</li>
      </ul>
    </div>
  </section>
</div>
</body>
</html>
```